ECommerce Site Redesign: overall site and specific pages

We have a website that has been in operation for 6+ years, and it's time for a visual refresh.

Our current website is located at http://qlt.example

The only significant functional change will be the movement of the persistent vertical navigation bar from the left side up to a categorized horizontal navigation menu. I've attached a rough mockup of how we want this positioned.

No coding necessary; just PSDs. The attached ROUGH MENU MOCKUP.PSD contains a layer with our logo on white should you wish to include it in your submissions.

Target Market(s)

We are an outdoor retailer focused on the high end of the market. We have a general color scheme on our site which we'd like to keep, but various elements need to be made consistent and more aesthetically pleasing.

Our brand is very important to us, and the site design must reflect our values of high quality and affluence. We cater to outdoor enthusiasts, hikers, back packers, and general high end apparel consumers.

Requirements
Must have
• In order to address the issue of consistency, we require strict design guidelines, including font sizing, element spacing, etc.

We require 7 page design templates for:

1.) overall site template - see http://qlt.example for current.
* narrow static header bar (NEW)
* footer (KEEP SAME/SIMILAR)
* background
* body
* mini-cart (collapsed and expanded)
* promotion panel (ad box, rotating featured items)
* horizontal navigation bars (expanded/collapsed, grouped by 7 main categories) - see attached ROUGH MENU MOCKUP and see additional notes.
* recently viewed products

2.) product page (see http://qlt.example/270599/frostwing_summit-hood-pure-plus-mens.aspx for current)
* product imagery/zoombox
* color, size, quantity selection
* add to cart button
* detail tabs
* In-store Availability info
* info panel near the add to cart box for exceptions including:
- Available to pick up in-store only
- Free shipping for your entire order when you purchase this item
- This item is over-sized; please contact a store directly
* "customers who bought this also bought" panel, grid listing of items

3.) product listings (category, search results, etc.)
* item thumbnails in grid format
* sidebar for refinement options (by supplier, by price, by size, etc.)

4.) generic information/content page (see http://qlt.example/t-returns.aspx)

5.) store locations page (see http://qlt.example/t-QLT.stores.04.aspx)
* store details
* map
* hours
* contact info
* local links
* contact form

6.) contact us form

7.) checkout (see attached current checkout screen shot)
* cart summary
* checkout steps

Any visual elements benefiting from hover effects will need to have both dimmed and hovered layers in the design.

```html
<!DOCTYPE html>
<html lang="en">
<head>
<meta charset="utf-8">
<title>Quillet Outfitters</title>
<link href="https://fonts.googleapis.com/css2?family=Ubuntu:wght@400;500&display=swap" rel="stylesheet">
<style>
:root{
  --purple:#9a52bb;
  --purple-dark:#7f3aa0;
  --purple-light:#b06fcf;
  --lilac:#e4d4ec;
  --text:#555;
  --muted:#8a8a8a;
  --link:#9a52bb;
  --line:#dcdcdc;
  --footer-bg:#d9d9d9;
}
*{box-sizing:border-box;margin:0;padding:0}
html,body{width:1024px;height:1200px;overflow:hidden}
body{font-family:"Ubuntu",sans-serif;color:var(--text);font-size:10px;
  background:linear-gradient(#e5d6ec 0,#f2ebf5 480px,#f7f3f8 900px,#fff 1200px);position:relative}
.abs{position:absolute}
.band{background:linear-gradient(var(--purple-light),var(--purple-dark));color:#fff}

.topbar{left:128px;top:17px;width:768px;height:41px;display:flex;align-items:center;padding:0 20px;font-size:11px}
.topbar .util{display:flex;align-items:center;gap:6px;margin-right:28px}
.topbar .cart{margin-left:auto;display:flex;align-items:center;gap:8px;font-size:10px}
.checkout{background:#f3f3f3;color:#333;border:1px solid #ccc;padding:4px 10px;font-size:10px;margin-left:10px}

.header{left:128px;top:58px;width:768px;height:74px;background:#fff;border-bottom:1px solid var(--line)}
.logo{position:absolute;left:16px;top:26px;display:flex;align-items:center;gap:6px;color:var(--purple-dark);font-size:15px;font-weight:500;letter-spacing:.5px;white-space:nowrap}
.logo i{width:9px;height:9px;background:var(--purple);display:block}
.search{position:absolute;left:580px;top:24px;width:172px;height:22px;background:var(--lilac);color:#777;font-size:10px;padding:5px 10px}
.search b{position:absolute;right:8px;top:3px;color:#444;font-weight:400;font-size:12px}

.nav{left:128px;top:133px;width:768px;height:37px;background:#fff;border-bottom:3px solid #ddcde6;display:flex;align-items:center;padding-left:15px;gap:28px;font-size:10.5px;color:#444}

.feature{left:128px;top:172px;width:768px;height:303px;background:#fff}
.crumb{position:absolute;left:16px;top:18px;font-size:10px;color:#777}
.crumb a{color:var(--link);text-decoration:none}
.hero{position:absolute;left:16px;top:45px;width:548px;height:240px;
  background:linear-gradient(120deg,#a55a3a 0,#8b6a55 30%,#c9c2b8 55%,#8c8478 80%,#5f5a52 100%)}
.hero .caption{position:absolute;left:0;bottom:0;height:42px;width:210px;background:var(--purple);color:#fff;font-size:14px;padding:11px 14px;
  clip-path:polygon(0 0,82% 0,100% 100%,0 100%)}
.featured{position:absolute;left:579px;top:45px;width:173px}
.featured h3{font-weight:400;font-size:11px;color:#555;padding-bottom:8px;border-bottom:1px solid var(--line);position:relative}
.featured h3 span{position:absolute;right:0;top:0;color:var(--purple);font-size:10px;letter-spacing:-2px}
.fitem{height:97px;border-bottom:1px solid var(--line);position:relative;background:linear-gradient(#fff,#f4f4f4)}
.fitem .thumb{position:absolute;left:10px;top:6px;width:50px;height:76px;background:linear-gradient(#2aa0c0,#157a98);border-radius:14px 14px 4px 4px}
.fitem .name{position:absolute;left:72px;top:11px;color:var(--link);font-size:9px;line-height:14px;width:96px}
.fitem .price{position:absolute;left:72px;top:57px;width:88px;height:18px;background:var(--purple);color:#fff;font-size:9px;text-align:center;line-height:18px;border-right:2px solid var(--purple-dark)}

.boxhead{height:29px;font-size:10px;padding:8px 16px}
.side{left:128px;width:188px;background:#fff;border:1px solid var(--line)}
.side .boxhead{margin:-1px -1px 0}
.side ul{list-style:none;padding:10px 15px;font-size:9.5px;line-height:19.2px;color:#555}
.side ul span{color:var(--link);margin-left:4px}
.side hr{border:0;border-top:1px dashed #ccc;margin:8px 0 9px}

.latest{left:332px;top:488px;width:564px}
.card{position:absolute;width:172px;height:212px;background:#fff;border:1px solid var(--line);box-shadow:0 1px 2px rgba(0,0,0,.12)}
.card .img{position:absolute;left:34px;top:14px;width:88px;height:136px;border-radius:30px 30px 14px 14px;background:linear-gradient(#4a4a4e,#1f1f22)}
.card .brand{position:absolute;right:2px;top:164px;font-size:8px;color:#222;letter-spacing:.3px}
.card .name{position:absolute;left:10px;top:162px;font-size:11px;color:#666}
.card .strip{position:absolute;left:0;right:0;bottom:0;height:35px;background:linear-gradient(#f6f6f6,#eaeaea);border-top:1px solid var(--line)}
.card .price{position:absolute;left:10px;top:11px;font-size:11px;color:var(--link)}
.card .btn{position:absolute;right:7px;top:6px;width:68px;height:18px;background:var(--purple);color:#fff;font-size:9px;text-align:center;line-height:18px;border-right:2px solid var(--purple-dark)}

.footer{left:128px;top:973px;width:768px;height:227px;background:var(--footer-bg)}
.footer .heads{height:36px;position:relative;font-size:11.5px}
.footer .heads span{position:absolute;top:11px}
.col{position:absolute;top:50px;font-size:9px;line-height:19.2px;color:#555;list-style:none}
.flogo{position:absolute;left:16px;top:66px;width:170px;color:var(--purple-dark);font-size:13px;font-weight:500;letter-spacing:.5px;display:flex;align-items:center;gap:6px;white-space:nowrap}
.flogo i{width:8px;height:8px;background:var(--purple);display:block;flex:none}
.social{position:absolute;left:16px;display:flex;align-items:flex-start;gap:12px;font-size:9px;line-height:14px;color:#555}
.sq{width:24px;height:24px;display:block;flex:none}
.copy{position:absolute;left:204px;top:205px;font-size:8.5px;color:#555}
</style>
</head>
<body>

<div class="abs topbar band">
  <div class="util">
    <svg width="16" height="18" viewBox="0 0 16 18"><path d="M8 1a6 6 0 0 0-6 6c0 4.5 6 10 6 10s6-5.5 6-10a6 6 0 0 0-6-6z" fill="#d8b9e6"/><circle cx="8" cy="7" r="2.3" fill="#a05cc0"/></svg>
    Find a Store
  </div>
  <div class="util">
    <svg width="18" height="18" viewBox="0 0 18 18"><path d="M13 1l3 3-9 13-3-2 2-6z" fill="#d8b9e6"/></svg>
    Contact Us
  </div>
  <div class="cart">
    <svg width="20" height="16" viewBox="0 0 20 16"><path d="M1 2h3l2 9h11l2-7H5" fill="none" stroke="#d8b9e6" stroke-width="1.5"/><circle cx="8" cy="14" r="1.4" fill="#d8b9e6"/><circle cx="16" cy="14" r="1.4" fill="#d8b9e6"/></svg>
    Your Cart Contains 3items
    <span class="checkout">Checkout</span>
  </div>
</div>

<div class="abs header">
  <div class="logo"><i></i>QUILLET OUTFITTERS</div>
  <div class="search">Search<b>›</b></div>
</div>

<nav class="abs nav">
  <span>Home</span><span>Women</span><span>Mens</span><span>Gear</span><span>Ultra light</span><span>Inspire</span><span>Review</span><span>On Sale</span>
</nav>

<section class="abs feature">
  <div class="crumb"><a>Home</a> &gt; First title</div>
  <div class="hero" role="img" aria-label="Trail runner in a pink jacket running among red rocks and frosted trees">
    <div class="caption">Never Stop Running</div>
  </div>
  <div class="featured">
    <h3>Today's Featured Items<span>◀ ▶</span></h3>
    <div class="fitem">
      <div class="thumb" role="img" aria-label="Teal women's hooded jacket"></div>
      <div class="name">Nimbus SV Hoody - Womens</div>
      <div class="price">$279.95 (CAD)</div>
    </div>
    <div class="fitem">
      <div class="thumb" role="img" aria-label="Teal women's hooded jacket"></div>
      <div class="name">Nimbus SV Hoody - Womens</div>
      <div class="price">$279.95 (CAD)</div>
    </div>
  </div>
</section>

<aside class="abs side" style="top:488px;height:296px">
  <div class="boxhead band">Browse by Category</div>
  <ul>
    <li>Women's Clothing<span>(879)</span></li>
    <li>Women's Footwear<span>(344)</span></li>
    <li>Men's Clothing<span>(1053)</span></li>
    <li>Men's Footwear<span>(392)</span></li>
    <li>Sunglasses<span>(166)</span></li>
    <hr>
    <li>Backpacks<span>(879)</span></li>
    <li>Hydration<span>(879)</span></li>
    <li>Tents, Tarps &amp; Bivys<span>(879)</span></li>
    <li>Sleeping Bags &amp; Mats<span>(879)</span></li>
    <li>Poles, Lights, &amp; Tools<span>(879)</span></li>
    <li>Women's Clothing<span>(879)</span></li>
  </ul>
</aside>

<aside class="abs side" style="top:797px;height:157px">
  <div class="boxhead band">Browse by Category</div>
  <ul>
    <li>Trail Journal Awards</li>
    <li>Spotlight</li>
    <li>Tropical Travel</li>
    <li>Ultralight Gear</li>
  </ul>
</aside>

<section class="abs latest">
  <div class="boxhead band">Latest Products</div>
  <div class="card" style="left:0;top:34px"><div class="img" role="img" aria-label="Black daypack"></div><span class="brand">RIDGELINE</span><span class="name">Vesta 22</span><div class="strip"><span class="price">$179.95 (CAD)</span><span class="btn">View Details</span></div></div>
  <div class="card" style="left:188px;top:34px"><div class="img" role="img" aria-label="Black daypack"></div><span class="brand">RIDGELINE</span><span class="name">Vesta 22</span><div class="strip"><span class="price">$179.95 (CAD)</span><span class="btn">View Details</span></div></div>
  <div class="card" style="left:376px;top:34px"><div class="img" role="img" aria-label="Black daypack"></div><span class="brand">RIDGELINE</span><span class="name">Vesta 22</span><div class="strip"><span class="price">$179.95 (CAD)</span><span class="btn">View Details</span></div></div>
  <div class="card" style="left:0;top:254px"><div class="img" role="img" aria-label="Black daypack"></div><span class="brand">RIDGELINE</span><span class="name">Vesta 22</span><div class="strip"><span class="price">$179.95 (CAD)</span><span class="btn">View Details</span></div></div>
  <div class="card" style="left:188px;top:254px"><div class="img" role="img" aria-label="Black daypack"></div><span class="brand">RIDGELINE</span><span class="name">Vesta 22</span><div class="strip"><span class="price">$179.95 (CAD)</span><span class="btn">View Details</span></div></div>
  <div class="card" style="left:376px;top:254px"><div class="img" role="img" aria-label="Black daypack"></div><span class="brand">RIDGELINE</span><span class="name">Vesta 22</span><div class="strip"><span class="price">$179.95 (CAD)</span><span class="btn">View Details</span></div></div>
</section>

<footer class="abs footer">
  <div class="heads band">
    <span style="left:16px">Social Media</span>
    <span style="left:204px">Quillet Outfitters Stores</span>
    <span style="left:392px">Site Services</span>
    <span style="left:518px">My QLT</span>
    <span style="left:645px">About QLT</span>
  </div>
  <div class="flogo"><i></i>QUILLET OUTFITTERS</div>
  <div class="social" style="top:104px"><span class="sq" style="background:#3b5a98"></span>Quillet Outfitters on<br>Social Page</div>
  <div class="social" style="top:144px"><span class="sq" role="img" aria-label="Portrait of the company president" style="background:linear-gradient(#b9a596,#8d7f74)"></span>Message from our President</div>
  <div class="social" style="top:178px"><svg class="sq" viewBox="0 0 24 24"><rect width="24" height="24" rx="4" fill="#3f7fd6"/><rect x="5" y="7" width="14" height="10" fill="#fff"/><path d="M5 7l7 6 7-6" fill="none" stroke="#3f7fd6" stroke-width="1.2"/></svg>Email our president</div>
  <ul class="col" style="left:204px"><li>Abbotsford</li><li>Canmore</li><li>Courtenay</li><li>Medicine Hat</li><li>Nanaimo</li><li>Squamish</li><li>Vancouver</li></ul>
  <ul class="col" style="left:289px"><li>Nelson</li><li>New Denver</li><li>Red Deer</li><li>Revelstoke</li><li>Smithers</li><li>Victoria/Langford</li></ul>
  <ul class="col" style="left:392px"><li>Privacy and Security</li><li>Return Policy</li><li>Shipping Rates</li><li>Terms &amp; Conditions</li><li>Site Map</li></ul>
  <ul class="col" style="left:518px"><li>My QLT Account Info</li><li>My Address Change</li><li>Recent Order History</li></ul>
  <ul class="col" style="left:645px"><li>About Us</li><li>FAQs</li><li>Contact Us</li></ul>
  <div class="copy">(C) 2012 Quillet Outfitters Inc. ALL RIGHTS RESERVED</div>
</footer>

</body>
</html>
```